Quorva - corporate Business Card

We need a good look and innovative business card for a new start up company based in Los Angeles called "Quorva". We are in a payment business, including payment card, app, and ewallet. We are expert in online payment and Card not present (CNP) transaction.
We need an innovative, modern business card.

Our logo font is Aero Matics

Target Market(s)

Startup - Bank - Online Payment - Card Manufacturing

Industry/Entity Type

Startup

Contact Information for Business Card

phone: 555 014 7396 - Address: 4172 Marlowe blvd, Tarrow Heights, NV 89145

Requirements
Must have
• Message: innovative, professional, expert, high tech, trust, online payment expert, security
Nice to have
• no comment
Should not have
• no Comment

```html
<!DOCTYPE html>
<html lang="en">
<head>
<meta charset="utf-8">
<title>Quorva – Business Card</title>
<link href="https://fonts.googleapis.com/css2?family=Exo+2:wght@500;600&family=Open+Sans:wght@400;600&display=swap" rel="stylesheet">
<style>
  :root {
    --brand-red: #b81f2d;
    --card-white: #fbfbfb;
    --ring-white: #f3f3f3;
    --ink: #1e1e1e;
    --backdrop: #e9e7e5;
  }
  * { margin: 0; padding: 0; box-sizing: border-box; }
  html, body { width: 1200px; height: 900px; overflow: hidden; }
  body { background: var(--backdrop); position: relative; font-family: "Open Sans", sans-serif; }

  .card {
    position: absolute;
    width: 555px;
    height: 345px;
    border-radius: 16px;
    overflow: hidden;
    box-shadow: 0 6px 18px rgba(0,0,0,0.18);
  }
  .card-front { left: 238px; top: 60px; background: var(--card-white); }
  .card-back { left: 460px; top: 520px; background: var(--brand-red); }

  .front-art { position: absolute; inset: 0; }

  .brand { position: absolute; left: 31px; top: 30px; display: flex; align-items: center; gap: 12px; }
  .brand-dot { width: 66px; height: 66px; border-radius: 50%; background: var(--brand-red); }
  .brand-name {
    font-family: "Exo 2", sans-serif; font-weight: 600; font-size: 46px;
    color: var(--brand-red); letter-spacing: 1px; line-height: 1;
  }

  .holder { position: absolute; left: 32px; top: 146px; }
  .holder-name { font-family: "Exo 2", sans-serif; font-weight: 600; font-size: 24px; color: var(--brand-red); line-height: 1.1; }
  .holder-role { font-size: 16px; color: var(--ink); margin-top: 2px; }

  .contacts { position: absolute; left: 32px; top: 208px; list-style: none; }
  .contacts li { display: flex; align-items: center; gap: 9px; font-size: 16px; color: var(--ink); height: 25px; }
  .contact-icon { width: 22px; height: 22px; flex: none; }

  .address { position: absolute; left: 32px; top: 265px; font-size: 15.5px; line-height: 22px; color: var(--ink); font-style: normal; }

  .back-seal {
    position: absolute; left: 190px; top: 83px; width: 180px; height: 180px; border-radius: 50%;
    background: var(--ring-white);
    box-shadow: 1px 2px 3px rgba(0,0,0,0.45);
  }
</style>
</head>
<body>

<section class="card card-front" aria-label="Business card front">
  <svg class="front-art" width="555" height="345" viewBox="0 0 555 345" aria-hidden="true">
    <rect x="407" y="0" width="148" height="345" fill="var(--brand-red)"/>
    <circle cx="402" cy="173" r="112" fill="var(--ring-white)"/>
    <circle cx="402" cy="173" r="78" fill="var(--brand-red)"/>
  </svg>

  <div class="brand">
    <span class="brand-dot"></span>
    <span class="brand-name">Quorva</span>
  </div>

  <div class="holder">
    <p class="holder-name">Dara Whitcombe</p>
    <p class="holder-role">Director</p>
  </div>

  <ul class="contacts">
    <li>
      <svg class="contact-icon" viewBox="0 0 22 22" aria-hidden="true">
        <circle cx="11" cy="11" r="11" fill="var(--brand-red)"/>
        <rect x="7.5" y="4.5" width="7" height="13" rx="1.5" fill="none" stroke="#fff" stroke-width="1.4"/>
        <circle cx="11" cy="15.3" r="0.8" fill="#fff"/>
      </svg>
      555 014 7396
    </li>
    <li>
      <svg class="contact-icon" viewBox="0 0 22 22" aria-hidden="true">
        <circle cx="11" cy="11" r="11" fill="var(--brand-red)"/>
        <circle cx="11" cy="11" r="6" fill="none" stroke="#fff" stroke-width="1.4"/>
        <path d="M5 11h12M11 5c-2.5 3-2.5 9 0 12M11 5c2.5 3 2.5 9 0 12" fill="none" stroke="#fff" stroke-width="1.1"/>
      </svg>
      www.quorva.com
    </li>
  </ul>

  <address class="address">
    4172 Marlowe blvd,<br>
    Tarrow Heights, NV 89145
  </address>
</section>

<section class="card card-back" aria-label="Business card back">
  <div class="back-seal"></div>
</section>

</body>
</html>
```